I need a humorous Regency romantic mystery ebook cover suitable for pagora, vell etc.

I need an ebook cover for the re-release of my humorous regency romantic mystery suitable for ebook and soft cover hard copy. No bare chests, clinches, etc. the cover should appeal to wide range of readers. Open to graphic and silhouette art as well as more traditional. Female blonde and blue, intelligent and sassy, male brown and brown, athletic, former military. Key items in story: notes written in Norse runes, tea services. Important settings: heroine climbing out a window in yellow dress, book room of Ashgrove museum, heroine finding body under mermaid shaped fountain. It is important to convey the humor and mystery aspect of the story. Both characters are familiar with dueling pistols. Title: Wool and Whispers

Target Market(s)

general readership, regency romance readers, mystery readers

Font styles to use
Script

Requirements
Must have
• Indications of humor, Regency period, and that it is a mystery. If using characters: Female:blonde and blue, intelligent, sassy, Male:brown and brown, military bearing, Fell free to use whatever text format you feel appropriate. There was no place to indicate this below. Title: Wool and Whispers sub line A Regency romantic mystery, Author: Marjorie Quillby
Nice to have
• Major clues: notes written in Norse runes.
• Character activity: Female finding body under fountain, climbing out window in yellow Regency evening dress.
• Major settings: both characters looking into glass cases of Book Room of museum, having civilized tea with pistols hidden under pillows on settee. Or maybe the artist would like to experiment with Regency silhouette images ala back to back male female with pistols and tea cups. Have fun just keep it regency, humorous, and balanced between mystery and romance
Should not have
• No clinches, bare chests, sultry kisses, etc.

```html
<!DOCTYPE html>
<html lang="en">
<head>
<meta charset="utf-8">
<title>Wool and Whispers — A Regency Romantic Mystery</title>
<link rel="stylesheet" href="https://fonts.googleapis.com/css2?family=Cinzel:wght@400;500&display=swap">
<style>
  :root {
    --crimson: #c01f2f;
    --title-red: #b3202c;
    --grey-word: #8f9296;
    --ink: #2b2b2e;
    --rule: #a9c2d8;
    --paper-light: #f7f8f9;
    --paper-edge: #c9ccd0;
    --brass: #a98b58;
    --barrel: #5a4a3c;
    --ivory: #ecdcb8;
    --porcelain: #f3f3f3;
    --tea: #b8421a;
  }
  html, body {
    margin: 0;
    padding: 0;
    width: 796px;
    height: 1200px;
    overflow: hidden;
    background: var(--paper-edge);
  }
  .cover {
    position: relative;
    width: 796px;
    height: 1200px;
    overflow: hidden;
    background: radial-gradient(ellipse at 52% 42%, var(--paper-light) 0%, #eceef0 45%, var(--paper-edge) 100%);
    font-family: "Cinzel", "Times New Roman", serif;
  }
  .cover-art {
    position: absolute;
    inset: 0;
  }
  .title {
    position: absolute;
    left: 0;
    right: 0;
    margin: 0;
    text-align: center;
    color: var(--title-red);
    font-weight: 400;
    line-height: 1;
  }
  .title-line-one {
    top: 238px;
    font-size: 142px;
    letter-spacing: 2px;
  }
  .title-and {
    font-size: 44px;
    color: var(--grey-word);
    letter-spacing: 1px;
    margin-left: 4px;
  }
  .title-line-two {
    top: 390px;
    font-size: 104px;
    letter-spacing: 4px;
  }
  .rule {
    position: absolute;
    left: 80px;
    width: 652px;
    height: 1px;
    background: var(--rule);
  }
  .rule-top { top: 521px; }
  .rule-bottom { top: 577px; }
  .subtitle {
    position: absolute;
    top: 536px;
    left: 0;
    right: 0;
    margin: 0;
    text-align: center;
    font-size: 22px;
    letter-spacing: 5px;
    color: var(--ink);
    font-weight: 400;
  }
  .author {
    position: absolute;
    top: 608px;
    left: 0;
    right: 0;
    margin: 0;
    text-align: center;
    font-size: 46px;
    letter-spacing: 3px;
    color: var(--title-red);
    font-weight: 400;
  }
</style>
</head>
<body>
  <main class="cover">
    <svg class="cover-art" width="796" height="1200" viewBox="0 0 796 1200" xmlns="http://www.w3.org/2000/svg">
      <defs>
        <linearGradient id="pistol-tone" x1="0" y1="0" x2="1" y2="0">
          <stop offset="0" stop-color="var(--barrel)"/>
          <stop offset="0.5" stop-color="var(--barrel)"/>
          <stop offset="0.55" stop-color="var(--brass)"/>
          <stop offset="0.78" stop-color="var(--brass)"/>
          <stop offset="0.82" stop-color="var(--ivory)"/>
          <stop offset="1" stop-color="var(--ivory)"/>
        </linearGradient>
        <radialGradient id="teacup-tone" cx="0.5" cy="0.5" r="0.5">
          <stop offset="0" stop-color="var(--tea)"/>
          <stop offset="0.5" stop-color="var(--tea)"/>
          <stop offset="0.56" stop-color="var(--porcelain)"/>
          <stop offset="1" stop-color="#e4e4e4"/>
        </radialGradient>
      </defs>

      <polygon class="corner-band corner-top" points="0,0 640,0 0,262" fill="var(--crimson)"/>
      <polygon class="corner-band corner-bottom" points="796,1200 796,880 180,1200" fill="var(--crimson)"/>

      <g class="pistol pistol-top" role="img" aria-label="Antique pistol with brass frame and ivory grip, lying diagonally across the top corner">
        <rect x="-60" y="-46" width="880" height="92" rx="10" fill="url(#pistol-tone)"
              transform="translate(380 150) rotate(-21)"/>
      </g>

      <g class="pistol pistol-bottom" role="img" aria-label="Antique pistol with brass frame and ivory grip, lying diagonally across the bottom corner, pointing up and right">
        <rect x="-60" y="-46" width="620" height="92" rx="10" fill="url(#pistol-tone)"
              transform="translate(560 1000) rotate(-38) scale(-1 1)"/>
      </g>

      <g class="teacup" role="img" aria-label="White teacup of red tea on a saucer, seen from above">
        <circle cx="393" cy="780" r="135" fill="url(#teacup-tone)"/>
      </g>
    </svg>

    <h1 class="title title-line-one">WOOL<span class="title-and">AND</span></h1>
    <p class="title title-line-two">WHISPERS</p>

    <div class="rule rule-top"></div>
    <p class="subtitle">A REGENCY ROMANTIC MYSTERY</p>
    <div class="rule rule-bottom"></div>

    <p class="author">MARJORIE QUILLBY</p>
  </main>
</body>
</html>
```